Business Card Design

We are a company that provides stump grinding services for residential and commercial clients. Looking for a simple business card design that may have some type of graphic on the card that will tie in with the Tamsen name(Grizzly Bear, Paw Print, etc) . Possibly some foliage wrapping around part of the card? Would like to have a simple design that stands out because it is unique. We are working on getting the website set up and there is a simple graphic on the top of the page that came to mind when I mentioned the leaves.

Industry/Entity Type

Business

Contact Information for Business Card

Tamsen Stump Grinding 303-257-4788KodiakStumps.Com

Font styles to use
Serif

Requirements
Must have
• Business name
• Website Address
• Phone Number
Nice to have
• Graphics that would be associated with a Tamsen bear.
Should not have
• Nothing frilly

```html
<!DOCTYPE html>
<html lang="en">
<head>
<meta charset="utf-8">
<title>Tamsen Stump Grinding — Business Card</title>
<link rel="stylesheet" href="https://fonts.googleapis.com/css2?family=EB+Garamond:wght@400;500;700&family=Montserrat:wght@400&display=swap">
<style>
  :root {
    --backdrop: #1f1f1f;
    --card-white: #ffffff;
    --leaf-light: #a9c46a;
    --leaf-mid: #6f8f45;
    --leaf-dark: #3d5530;
    --leaf-sky: #8fb7c4;
    --forest-dark: #1c1e1f;
    --forest-mid: #3a3c3d;
    --forest-trunk: #5a5552;
    --bear-brown: #6e4a2e;
    --bear-dark: #3f2a1b;
    --text-light: #ffffff;
    --text-dark: #141414;
  }
  * { margin: 0; padding: 0; box-sizing: border-box; }
  html, body {
    width: 1200px;
    height: 902px;
    overflow: hidden;
    background: var(--backdrop);
  }
  .business-card {
    position: absolute;
    left: 80px;
    top: 147px;
    width: 1040px;
    height: 608px;
    background: var(--card-white);
    overflow: hidden;
  }
  .foliage-banner {
    position: absolute;
    left: 0; top: 0;
    width: 100%;
    height: 236px;
    background:
      radial-gradient(ellipse at 85% 10%, var(--leaf-sky) 0%, transparent 35%),
      radial-gradient(ellipse at 20% 60%, var(--leaf-light) 0%, transparent 55%),
      radial-gradient(ellipse at 70% 70%, var(--leaf-light) 0%, transparent 50%),
      linear-gradient(160deg, var(--leaf-mid), var(--leaf-dark) 60%, var(--leaf-mid));
  }
  .company-name {
    position: absolute;
    left: 0; top: 88px;
    width: 100%;
    text-align: center;
    font-family: "EB Garamond", serif;
    font-weight: 400;
    font-size: 50px;
    letter-spacing: 1px;
    color: var(--text-light);
    text-shadow: 0 1px 3px rgba(0,0,0,0.35);
  }
  .tagline {
    position: absolute;
    left: 0; top: 161px;
    width: 100%;
    display: flex;
    justify-content: center;
    align-items: center;
    gap: 12px;
    font-family: "Montserrat", sans-serif;
    font-size: 16px;
    color: var(--text-light);
  }
  .tagline-rule {
    width: 36px;
    height: 1px;
    background: var(--text-light);
  }
  .forest-scene {
    position: absolute;
    left: 0; top: 250px;
    width: 100%;
    height: 293px;
    background:
      linear-gradient(90deg, transparent 27%, rgba(90,85,82,0.55) 29%, rgba(90,85,82,0.55) 35%, transparent 37%),
      linear-gradient(90deg, transparent 60%, rgba(90,85,82,0.35) 62%, rgba(90,85,82,0.35) 67%, transparent 69%),
      radial-gradient(ellipse at 50% 30%, var(--forest-mid) 0%, var(--forest-dark) 75%);
  }
  .bear-left {
    position: absolute;
    left: 0; top: 105px;
    width: 330px;
    height: 188px;
    border-radius: 50% 55% 0 0 / 60% 70% 0 0;
    background: radial-gradient(ellipse at 45% 40%, var(--bear-brown), var(--bear-dark) 80%);
  }
  .bear-right {
    position: absolute;
    left: 780px; top: 100px;
    width: 210px;
    height: 193px;
    border-radius: 50% 50% 0 0 / 55% 55% 0 0;
    background: radial-gradient(ellipse at 50% 35%, #8a5a33, var(--bear-dark) 85%);
  }
  .contact-block {
    position: absolute;
    left: 0; top: 28px;
    width: 100%;
    text-align: center;
    font-family: "EB Garamond", serif;
    color: var(--text-light);
    text-shadow: 0 2px 3px rgba(0,0,0,0.8);
  }
  .employee-name {
    font-size: 40px;
    font-weight: 500;
    line-height: 44px;
  }
  .employee-title {
    font-size: 30px;
    line-height: 32px;
  }
  .contact-line {
    font-size: 29px;
    line-height: 41px;
  }
  .contact-list { margin-top: 36px; }
  .contact-label { font-weight: 700; }
  .website-band {
    position: absolute;
    left: 0; bottom: 0;
    width: 100%;
    height: 65px;
    display: flex;
    justify-content: center;
    align-items: center;
    font-family: "EB Garamond", serif;
    font-weight: 700;
    font-size: 30px;
    color: var(--text-dark);
  }
</style>
</head>
<body>
  <article class="business-card">
    <header class="foliage-banner" role="img" aria-label="Photograph of green and autumn leaves on branches">
      <h1 class="company-name">TAMSEN STUMP GRINDING</h1>
      <p class="tagline"><span class="tagline-rule"></span>DENVER TREE STUMP GRINDING SERVICES<span class="tagline-rule"></span></p>
    </header>

    <section class="forest-scene" role="img" aria-label="Dark misty forest with tall tree trunks and falling snow">
      <div class="bear-left" role="img" aria-label="Photograph of a brown grizzly bear walking"></div>
      <div class="bear-right" role="img" aria-label="Photograph of a roaring brown grizzly bear"></div>
      <div class="contact-block">
        <p class="employee-name">EMPLOYEE NAME</p>
        <p class="employee-title">Owner</p>
        <div class="contact-list">
          <p class="contact-line"><span class="contact-label">Phone:</span> 303-555-0146</p>
          <p class="contact-line"><span class="contact-label">Email:</span> hello@tamsenmail.com</p>
        </div>
      </div>
    </section>

    <footer class="website-band">www.TamsenStumps.Com</footer>
  </article>
</body>
</html>
```